Business Card Design for Varomir Facility Services

We are looking for a Business Card Design for the Company "Varomir Facility Services."
Front side:
- Company Logo (small)
- Company Name, address, pohone, website and personal data.
- white background, for text e.g. company colors (blue or green like in the logo)
Please use following data:
Company data:
Varomir Facility Services Kostelac
Birkenhaldweg 14
6330 Cham
www.varomir-fs.ch
Person data:
Tarik Kostelac
Geschäftsführer
+41 76 519 47 83
info@varomir-fs.ch
Back side:
could be colored in blue or green
please use a big logo sing and some smaller icons to say what is all beeing offered in facility services, like cleaning, maintenance cleaning
industrial cleaning, caretaking, gardening, disposal. There is no need for everyone of the icons if there are similar or an icon is standing for more of them.
colors to use:
blue: HEX 246BB0
green: HEX 52B33E

```html
<!DOCTYPE html>
<html lang="de">
<head>
<meta charset="utf-8">
<title>Varomir Facility Services – Business Card</title>
<link rel="stylesheet" href="https://fonts.googleapis.com/css2?family=Lato:wght@400;700&display=swap">
<style>
  :root {
    --brand-blue: #246BB0;
    --brand-green: #52B33E;
    --green-deep: #2BAE3A;
    --green-light: #7DC22A;
    --ink: #1f1f1f;
    --rule: #9a9a9a;
    --paper: #ffffff;
    --backdrop: #2a2a2a;
  }
  * { margin: 0; padding: 0; box-sizing: border-box; }
  html, body { width: 1200px; height: 1200px; overflow: hidden; }
  body {
    background: var(--backdrop);
    font-family: "Lato", sans-serif;
    position: relative;
  }
  .card {
    position: absolute;
    top: 310px;
    width: 366px;
    height: 594px;
    overflow: hidden;
  }
  .card--front { left: 234px; background: var(--paper); text-align: center; }
  .card--back { left: 628px; background: var(--brand-blue); }

  .brand-name {
    position: absolute;
    left: 0; right: 0; top: 170px;
    color: var(--brand-blue);
    font-weight: 700;
    text-transform: uppercase;
    line-height: 1.1;
  }
  .brand-name__main { display: block; font-size: 46px; letter-spacing: 3px; }
  .brand-name__sub { display: block; font-size: 20px; letter-spacing: 4px; }

  .person { position: absolute; left: 0; right: 0; top: 340px; }
  .person__name {
    color: var(--brand-blue);
    font-weight: 700;
    font-size: 20px;
    text-transform: uppercase;
    letter-spacing: 0.3px;
  }
  .person__role { font-size: 16px; color: var(--ink); margin-top: -2px; }

  .contact-icons {
    position: absolute; left: 87px; top: 396px;
    width: 190px; height: 24px;
  }
  .contact {
    position: absolute; left: 0; right: 0; top: 430px;
    font-size: 16px; line-height: 22px; color: var(--ink);
  }
  .rule {
    position: absolute; left: 88px; width: 195px; top: 502px;
    height: 1px; background: var(--rule);
  }
  .company {
    position: absolute; left: 0; right: 0; top: 514px;
    font-size: 17px; line-height: 22px; color: var(--ink);
  }

  .back-field { position: absolute; inset: 0; width: 366px; height: 594px; }
  .back-name {
    position: absolute; left: 0; right: 0; top: 230px;
    text-align: center; color: var(--paper);
    font-weight: 700; text-transform: uppercase; line-height: 1.1;
  }
  .back-name__main { display: block; font-size: 52px; letter-spacing: 3px; }
  .back-name__sub { display: block; font-size: 20px; letter-spacing: 4px; }
  .services {
    position: absolute; left: 0; right: 0; top: 492px;
    text-align: center; color: var(--paper);
    font-size: 15px; line-height: 19px; text-transform: uppercase;
    letter-spacing: 0.2px;
  }
</style>
</head>
<body>

<section class="card card--front" aria-label="Visitenkarte Vorderseite">
  <h1 class="brand-name">
    <span class="brand-name__main">Varomir</span>
    <span class="brand-name__sub">Facility Services</span>
  </h1>

  <div class="person">
    <p class="person__name">Tarik Kostelac</p>
    <p class="person__role">Geschäftsführer</p>
  </div>

  <svg class="contact-icons" viewBox="0 0 190 24" aria-hidden="true">
    <line x1="0" y1="12" x2="54" y2="12" stroke="#9a9a9a" stroke-width="1"/>
    <line x1="136" y1="12" x2="190" y2="12" stroke="#9a9a9a" stroke-width="1"/>
    <g fill="#246BB0">
      <circle cx="67" cy="12" r="11"/>
      <circle cx="94" cy="12" r="11"/>
      <circle cx="121" cy="12" r="11"/>
    </g>
    <!-- phone -->
    <path d="M61 8 q1-2 3-1 l1 2 q0 1-1 2 q1 2 3 3 q1-1 2-1 l2 1 q1 2-1 3 q-4 1-7-2 q-3-3-2-7z" fill="#fff"/>
    <!-- mail -->
    <rect x="87" y="7" width="14" height="10" fill="none" stroke="#fff" stroke-width="1.5"/>
    <path d="M87 7 l7 6 l7-6" fill="none" stroke="#fff" stroke-width="1.5"/>
    <!-- globe -->
    <circle cx="121" cy="12" r="6.5" fill="none" stroke="#fff" stroke-width="1.5"/>
    <ellipse cx="121" cy="12" rx="3" ry="6.5" fill="none" stroke="#fff" stroke-width="1.2"/>
    <line x1="114.5" y1="12" x2="127.5" y2="12" stroke="#fff" stroke-width="1.2"/>
  </svg>

  <div class="contact">
    <p>+41 76 519 47 83</p>
    <p>info@varomir-fs.ch</p>
    <p>www.varomir-fs.ch</p>
  </div>

  <div class="rule"></div>

  <address class="company" style="font-style: normal;">
    <p>Varomir Facility Services Kostelac</p>
    <p>Birkenhaldweg 14, 6330 Cham</p>
  </address>
</section>

<section class="card card--back" aria-label="Visitenkarte Rückseite">
  <svg class="back-field" viewBox="0 0 366 594" aria-hidden="true">
    <defs>
      <linearGradient id="greenField" x1="0" y1="1" x2="1" y2="0">
        <stop offset="0" stop-color="#2BAE3A"/>
        <stop offset="1" stop-color="#7DC22A"/>
      </linearGradient>
    </defs>
    <rect width="366" height="594" fill="url(#greenField)"/>
    <path d="M0 0 H366 V390 C240 404 80 388 0 332 Z" fill="#246BB0"/>
  </svg>

  <h2 class="back-name">
    <span class="back-name__main">Varomir</span>
    <span class="back-name__sub">Facility Services</span>
  </h2>

  <div class="services">
    <p>Cleaning &nbsp;|&nbsp; Maintenance Cleaning</p>
    <p>Industrial Cleaning</p>
    <p>Caretaking &nbsp;|&nbsp; Gardening &nbsp;|&nbsp; Disposal</p>
  </div>
</section>

</body>
</html>
```